Brightfield Ventures Inc. Letterhead

Creation of attractive and eye catching letterhead for a business start-up for the construction industry. Letterhead must relate to construction, but avoid standard hammer and tools in the design.

I forgot to add some details, sorry about that. Some pertinent info: Ph: 916-555-0187 brightfieldventures.example 448 Willowmere Ave, Ste 210 Folsom, CA 95999 info@brightfieldventures.example not sure if slogan should be in there" “Connecting construction professionals to create a purpose driven industry.” must be able to be used in word. Thanks!

```html
<!DOCTYPE html>
<html lang="en">
<head>
<meta charset="UTF-8">
<title>Brightfield Ventures Inc. Letterhead</title>
<link rel="stylesheet" href="https://fonts.googleapis.com/css2?family=Montserrat:wght@600&family=Open+Sans:wght@400&family=Arimo:wght@700&display=swap">
<style>
  :root {
    --backdrop: #e4e5e7;
    --paper: #ffffff;
    --navy: #1f2a6b;
    --red: #bf0d10;
    --ink: #2e2e2e;
  }
  * { box-sizing: border-box; margin: 0; padding: 0; }
  html, body { width: 1200px; height: 945px; overflow: hidden; background: var(--backdrop); }
  .letterhead {
    position: absolute; left: 282px; top: 18px;
    width: 636px; height: 909px;
    background: var(--paper);
    box-shadow: 0 4px 16px rgba(0,0,0,.12);
    font-family: "Open Sans", Arial, sans-serif;
    color: var(--ink);
  }
  .brand {
    position: absolute; top: 62px; left: 0; right: 0;
    display: flex; align-items: center; justify-content: center; gap: 8px;
    font-family: "Montserrat", sans-serif; font-weight: 600;
    font-size: 17px; letter-spacing: 1.5px; color: var(--navy); text-transform: uppercase;
  }
  .brand-square { width: 12px; height: 12px; background: var(--navy); }
  .letter-body { position: absolute; top: 212px; left: 64px; right: 60px; }
  .salutation { font-family: "Arimo", Arial, sans-serif; font-weight: 700; font-size: 14px; margin-bottom: 12px; color: #111; }
  .letter-body p { font-size: 12px; line-height: 1.3; margin-bottom: 14px; }
  .letter-body p:last-child { margin-bottom: 0; }
  .letter-body p.indented { padding-left: 36px; }
  .signature {
    position: absolute; top: 686px; left: 86px; width: 140px; height: 46px;
    background: linear-gradient(90deg, #f2f2f2, #e8e8e8); border-radius: 4px;
  }
  .footer-rule { position: absolute; left: 176px; right: 30px; top: 758px; height: 1.5px; background: var(--navy); }
  .contact { position: absolute; right: 36px; top: 772px; text-align: right; font-size: 10.5px; line-height: 1.7; }
  .contact-row { display: flex; justify-content: flex-end; gap: 12px; align-items: center; }
  .contact-row span { display: inline-flex; align-items: center; gap: 4px; }
  .contact svg { width: 10px; height: 10px; fill: var(--navy); }
  .footer-band { position: absolute; left: 0; right: 0; bottom: 0; height: 30px; background: var(--red); }
</style>
</head>
<body>
<main class="letterhead">
  <header class="brand"><span class="brand-square"></span>Brightfield Ventures</header>

  <section class="letter-body">
    <h1 class="salutation">Dear Mr. John,</h1>
    <p>Lorem Ipsum is simply dummy text of the printing and typesetting industry. Lorem Ipsum has been the industry's standard dummy text ever since the 1500s, when an unknown printer took a galley of type and scrambled it to make a type specimen book. It has survived not only five centuries, but also the leap into electronic typesetting, remaining essentially unchanged.</p>
    <p class="indented">The standard chunk of Lorem Ipsum used since the 1500s is reproduced below for those interested. Sections 1.10.32 and 1.10.33 from "de Finibus Bonorum et Malorum" by Cicero are also reproduced in their exact original form, accompanied by English versions from the 1914 translation by H. Rackham</p>
    <p>Lorem Ipsum is simply dummy text of the printing and typesetting industry. Lorem Ipsum has been the industry's standard dummy text ever since the 1500s, when an unknown printer took a galley of type and scrambled it to make a type specimen book. It has survived not only five centuries, but also the leap into electronic typesetting, remaining essentially unchanged. It was popularised in the</p>
    <p class="indented">The standard chunk of Lorem Ipsum used since the 1500s is reproduced below for those interested. Sections 1.10.32 and 1.10.33 from "de Finibus Bonorum et Malorum" by Cicero are also reproduced in their exact original form, accompanied by English versions from the 1914 translation by H. Rackham</p>
    <p class="indented">The standard chunk of Lorem Ipsum used since the 1500s is reproduced below for those interested. Sections 1.10.32 and 1.10.33 from "de Finibus Bonorum et Malorum" by Cicero are also reproduced in their exact original form.</p>
  </section>

  <div class="signature" role="img" aria-label="Handwritten signature"></div>

  <div class="footer-rule"></div>
  <footer class="contact">
    <div>Po. box 201, Street Name, City Name, Zip Code - 00000</div>
    <div class="contact-row">
      <span><svg viewBox="0 0 10 10"><path d="M2 0h2l1 3-1.5 1a6 6 0 0 0 2.5 2.5L7 5l3 1v2a2 2 0 0 1-2 2A8 8 0 0 1 0 2a2 2 0 0 1 2-2z"/></svg>1-254-555-0143</span>
      <span><svg viewBox="0 0 10 10"><path d="M0 2h10v6H0z M0 2l5 3 5-3" stroke="#fff" stroke-width=".8"/></svg>info@companyname.example</span>
      <span><svg viewBox="0 0 10 10"><circle cx="5" cy="5" r="5"/></svg>www.companyname.example</span>
    </div>
  </footer>
  <div class="footer-band"></div>
</main>
</body>
</html>
```